Flat bootstrap design for existing site

I'm looking for a modern flat design based around an existing logo. This has to be a custom design (no external templates), and implemented into a bootstrap framework.

The logo is attached as 2 versions - choose whichever you want, that flows better with whatever design you choose.

Added screenshots of the existing site (currently using the default bootstrap layouts). Please make your designs around those pages in the screenshots (i.e. the homepage only has the postal code input and the header). The active page has 3 screenshots, because I wanted to illustrate the other states that would be visible (in the table rows).

This is a moving/junk removal website, just for some context.

Here's some example websites (flat designs) that I like, just to give you an idea of what I'm after.

https://www.plimvora.com/
https://dacklow.com/
https://trevanu.com/
https://quobrintal.com/en/

Coding

Coded - Design and coding required

Number of Pages Required

5+ page

Colors

Designer to choose colors to be used in the design.

Requirements
Must have
• It must be a modern/simple flat design, that is built around the existing logo (attached).
• It has to be implemented using bootstrap.

```html
<!DOCTYPE html>
<html lang="en">
<head>
<meta charset="utf-8">
<title>HAULVEX – Booking</title>
<link href="https://fonts.googleapis.com/css2?family=Roboto:wght@400;500;700&family=Montserrat:wght@600;700;800&display=swap" rel="stylesheet">
<style>
:root{
  --sky:#38bdf2;
  --sky-deep:#1387d6;
  --purple:#5e55c6;
  --purple-btn:#6659c7;
  --ink:#3b3b4a;
  --muted:#9a9aa8;
  --line:#dcdfe8;
  --green:#8dc63f;
  --white:#fff;
}
*{box-sizing:border-box;margin:0;padding:0}
html,body{width:1200px;height:944px;overflow:hidden}
body{position:relative;background:var(--sky);font-family:"Roboto",sans-serif;color:var(--ink)}
.brand{position:absolute;left:144px;top:24px;display:flex;align-items:center;gap:10px;font-family:"Montserrat",sans-serif;font-weight:800;font-size:30px;color:var(--white);letter-spacing:1px}
.brand-dot{width:16px;height:16px;border-radius:50%;background:var(--white)}
.nav{position:absolute;top:22px;right:144px;display:flex;align-items:center;font-family:"Montserrat",sans-serif;font-weight:700;font-size:11px;letter-spacing:.6px;color:var(--white)}
.nav a{color:inherit;text-decoration:none;margin-left:26px}
.nav a:first-child{margin-left:0}
.nav .driver{background:var(--sky-deep);padding:11px 12px;margin-left:24px}
.nav .account{color:var(--purple);font-family:"Roboto",sans-serif;font-weight:500;font-size:13px;display:flex;align-items:center;gap:6px;margin-left:16px}
.avatar{width:18px;height:18px;border-radius:50%;background:var(--purple)}
.card{position:absolute;left:144px;top:102px;width:912px;height:678px;background:var(--white);box-shadow:0 6px 24px rgba(0,60,120,.15)}
.title{position:absolute;left:23px;top:29px;width:870px;font-size:19.2px;line-height:24px;font-weight:400;color:var(--purple);letter-spacing:-.1px}
.field{position:absolute;left:0;width:446px;display:flex;align-items:center}
.field label{width:68px;text-align:right;font-size:12px;font-weight:500;line-height:13px;color:var(--ink)}
.input{margin-left:10px;width:366px;height:36px;border:1px solid var(--line);padding:0 11px;display:flex;align-items:center;justify-content:space-between;font-size:12.5px;color:var(--ink)}
.input.ph{color:var(--muted)}
.input.active{border-color:var(--purple)}
.input.area{height:68px;align-items:flex-start;padding-top:10px}
.sel{width:10px;height:18px}
.btn-book{position:absolute;left:78px;top:617px;width:81px;height:36px;background:var(--purple-btn);color:var(--white);font-family:"Montserrat",sans-serif;font-weight:700;font-size:11.5px;letter-spacing:.8px;display:flex;align-items:center;justify-content:center}
.picker{position:absolute;left:468px;top:101px;width:420px;height:324px;border:1px solid var(--line)}
.picker-lead{position:absolute;left:22px;top:26px;width:320px;font-size:14px;line-height:19px;font-weight:500;color:var(--ink)}
.cal{position:absolute;left:14px;top:90px;width:218px}
.cal-head{display:flex;justify-content:space-between;align-items:center;color:var(--purple);font-size:12px;font-weight:500;height:20px;padding:0 4px}
.cal-grid{display:grid;grid-template-columns:repeat(7,31.2px);margin-top:5px}
.cal-grid span{height:24px;display:flex;align-items:center;justify-content:center;font-size:12px}
.cal-grid .dn{font-weight:700;font-size:11px;height:26px;margin-bottom:5px}
.cal-grid .out{color:var(--muted)}
.cal-grid .on{background:var(--sky);color:var(--white);margin:2px 3px;height:20px}
.time{position:absolute;left:272px;top:148px;font-size:12px;font-weight:700;color:var(--ink)}
.time .col{position:absolute;width:20px;text-align:center}
.time .arrow{position:absolute;width:20px;height:12px}
.ampm{position:absolute;left:349px;top:192px;width:26px;height:20px;background:var(--green);color:var(--white);font-size:12px;font-weight:700;display:flex;align-items:center;justify-content:center}
.scene{position:absolute;right:0;top:718px;width:150px;height:161px;border-radius:150px 0 0 0;background:linear-gradient(160deg,#7fd3f5,#5fc4ee)}
.footer{position:absolute;left:0;top:879px;width:1200px;height:65px;background:var(--white);border-bottom:6px solid var(--purple)}
.footer p{position:absolute;left:144px;top:25px;font-size:12px;color:var(--ink)}
.social{position:absolute;right:144px;top:21px;display:flex;gap:7px}
.social span{width:18px;height:18px;background:#8f93b4;border-radius:2px}
</style>
</head>
<body>
<div class="brand"><span class="brand-dot"></span>HAULVEX</div>
<nav class="nav">
  <a href="#">BOOK</a>
  <a href="#">HOW IT WORKS</a>
  <a href="#" class="driver">BECOME A DRIVER</a>
  <a href="#" class="account"><span class="avatar"></span>jordan@haulvex.com ⌄</a>
</nav>

<main class="card">
  <h1 class="title">BookinaWe have drivers near you, and waiting to pich up your stuff! Please fill in the details below to complete the booking</h1>

  <div class="field" style="top:101px"><label>First<br>Name</label><div class="input ph active">First Name<svg class="sel" viewBox="0 0 10 18"><path d="M2 6l3-3 3 3M2 12l3 3 3-3" fill="none" stroke="#5e55c6" stroke-width="1.4"/></svg></div></div>
  <div class="field" style="top:149px"><label>Last<br>Name</label><div class="input ph">Last Name</div></div>
  <div class="field" style="top:197px"><label>Email</label><div class="input ph">Email</div></div>
  <div class="field" style="top:245px"><label>Address</label><div class="input ph">Pickup Address</div></div>
  <div class="field" style="top:293px"><label>City</label><div class="input">London</div></div>
  <div class="field" style="top:341px"><label>Province</label><div class="input">Ontario<svg class="sel" viewBox="0 0 10 18"><path d="M2 6l3-3 3 3M2 12l3 3 3-3" fill="none" stroke="#5e55c6" stroke-width="1.4"/></svg></div></div>
  <div class="field" style="top:389px"><label>Postal<br>Code</label><div class="input">k2p4x8</div></div>
  <div class="field" style="top:437px"><label>Phone</label><div class="input ph">Phone</div></div>
  <div class="field" style="top:485px"><label>Packages</label><div class="input">Select Package<svg class="sel" viewBox="0 0 10 18"><path d="M2 6l3-3 3 3M2 12l3 3 3-3" fill="none" stroke="#5e55c6" stroke-width="1.4"/></svg></div></div>
  <div class="field" style="top:533px;align-items:flex-start"><label style="padding-top:11px">Describe</label><div class="input ph area">Describe items that ned to be removed</div></div>
  <div class="btn-book">BOOK</div>

  <section class="picker">
    <p class="picker-lead">Select the date and time that you would like the pick-up to happen.</p>
    <div class="cal">
      <div class="cal-head">
        <svg width="10" height="12" viewBox="0 0 10 12"><path d="M7 1 2 6l5 5" fill="none" stroke="#5e55c6" stroke-width="2"/></svg>
        <span>July 2017</span>
        <svg width="10" height="12" viewBox="0 0 10 12"><path d="M3 1l5 5-5 5" fill="none" stroke="#5e55c6" stroke-width="2"/></svg>
      </div>
      <div class="cal-grid">
        <span class="dn">Su</span><span class="dn">Mo</span><span class="dn">Tu</span><span class="dn">We</span><span class="dn">Th</span><span class="dn">Fr</span><span class="dn">Sa</span>
        <span class="out">25</span><span class="out">26</span><span class="out">27</span><span class="out">28</span><span class="out">29</span><span class="out">30</span><span>1</span>
        <span>2</span><span>3</span><span>4</span><span>5</span><span>6</span><span>7</span><span>8</span>
        <span>9</span><span>10</span><span>11</span><span>12</span><span class="on">13</span><span>14</span><span>15</span>
        <span>16</span><span>17</span><span>18</span><span>19</span><span>20</span><span>21</span><span>22</span>
        <span>23</span><span>24</span><span>25</span><span>26</span><span>27</span><span>28</span><span>29</span>
        <span>30</span><span>31</span><span class="out">1</span><span class="out">2</span><span class="out">3</span><span class="out">4</span><span class="out">5</span>
      </div>
    </div>
    <div class="time">
      <svg class="arrow" style="left:0;top:0" viewBox="0 0 20 12"><path d="M5 9l5-5 5 5" fill="none" stroke="#5e55c6" stroke-width="2"/></svg>
      <svg class="arrow" style="left:42px;top:0" viewBox="0 0 20 12"><path d="M5 9l5-5 5 5" fill="none" stroke="#5e55c6" stroke-width="2"/></svg>
      <span class="col" style="left:0;top:46px">08</span>
      <span class="col" style="left:21px;top:46px">:</span>
      <span class="col" style="left:42px;top:46px">30</span>
      <svg class="arrow" style="left:0;top:84px" viewBox="0 0 20 12"><path d="M5 3l5 5 5-5" fill="none" stroke="#5e55c6" stroke-width="2"/></svg>
      <svg class="arrow" style="left:42px;top:84px" viewBox="0 0 20 12"><path d="M5 3l5 5 5-5" fill="none" stroke="#5e55c6" stroke-width="2"/></svg>
    </div>
    <div class="ampm">PM</div>
  </section>
</main>

<div class="scene" role="img" aria-label="Illustration of a removal driver beside a house and a branded van on a green hill"></div>

<footer class="footer">
  <p>© 2017 HAULVEX. All rights reserved.</p>
  <div class="social"><span></span><span></span><span></span></div>
</footer>
</body>
</html>
```